Corporate website design needed

We need a Contemporary Industrial/Tech/Logistics Website design to match our logistic client's business. Our client consults and build logistics solutions that they manage but they are not a typical 3PL (3rd party logistics company) which is primarily engaged in moving boxes.
PSD file only for now, home and default templates.
COMPANY CHARACTER
DESIGN LOOK AND FEEL
• The design should also be modern and visually well organized — employing a combination of visual devices and info graphics. Keep it light and not too heavy but strong/ professional. And unique.
• The design should go beyond the typical industrial pick and pack 3PL representing [Logistics Company] as a High Tech/IT logistics company.
Some examples although these are not right for this client because they have much more content and present themselves more as a 3pl.
http://www.vobrelink-hub.example/ (More right then wrong - Like this but simplified)
http://www.durmaxfreight.example (Ugly)
http://www.tpwallerton.example (More right then wrong but different focus)
http://www.pelhamrye.example/ Too 3PL trucking… We want a bit ore high level approach
The difference, the design should be a fusion in core concepts that culminate in a design which implies the following attributes. Tech (Big data / analytics / software), Consultancy (Solutions, SME, Leader), 3PL Industry vertical solutions.
NOTE: The visualization of “tech” is not “1” and “0”, but more “software and analytics” Perhaps more like www.navimetra.example.
• They need to be seen as a solutions provider in Logistics and as in Subject matter experts
TONE
The tone needs to exude professionalism, expertise, though leadership along with technical and executional excellence.
Experienced
Knowledgeable
Confident
Determined
Straightforward
WEBSITE OBJECTIVES
• Focus C-Suite executives and logistics managers’ attention on [Logistics Company]s commanding knowledge and expertise, and unique approach to supply chain solutions producing more RFP wins
• Create an easy to scan design which decreases the reliance on text through featured text, summaries, and smaller “chunked” size bits of information.
• Convey [Logistics Company] as high-tech 3PL solutions developer and services provider with a ‘high-touch’ consultative approach.
• Showcase [Logistics Company]’s value propositions. (See Slider Content)
• Showcase [Logistics Company]’s expertise in logistical analytics.
• Gain recognition as an industry leader in evolutionary new space (supply chain 2.0)
WEBSITE STRATEGY
• Reduce reliance on text (at least within initial entry points for each section)
• Typography: Watch text line lengths and readability, bolder fonts. NO SERIFS
• Generally, create a click-through format so that users who want more details can find it, and those who don’t can get a snapshot without clicking through.
• Increase visual content through info graphics and some dynamic content, photography
• Better utilize the space on each page (e.g., add visual interest, photography and iconography where appropriate to break up copy blocks and maintain readable line lengths).
COLOR SCHEME
• Create a more engaging color scheme (the logo will remain the same under all circumstances).
• Red / grayscale may work…. Not too dark or heavy. Not too much red. Ex. quiltora.example
• Also try blues and greys. They seem to like that. Open to suggestions but don’t get to crazy. Red is in their logo but too much may be a problem.
PHOTOGRAPHY
Yes. And I will upload some.
If you pick photography please be sure to note Which stock house used and the image number!
CONTENT
The content will be presented in a more hierarchical format — with lead-ins, paragraph and section headers and navigational cues to expand lengthier content allowing the visitor to more easily scan the website. No case studies, No Social media, News while on the home page should not be over emphasized. They don't post a lot so it gets dated quickly ...
I will be uploading a wire frame and other elements.
NOTE: I uploaded my EXAMPLE mock up which is close but not close enough.
I am not a great designer. So I am looking for an alternative that exceed my design ability! These examples show the basic layout but I really want some varied alternatives.
The colors are inconsistent and type not quite right. The grey bar at top is not right and should probably go away.
Please pull the basic elements in the example together into a great design.
If you have questions please contact me.
i will upload some photography tomorrow that may be of use.
Thanks!
Updates
Hi All,
We are still evaluating the submitted designs. Sorry for the delay.
Target Market(s)
This website is primarily a validation website. Few new customers will search and find them as such...
The site should be Focused on C-Suite executives and logistics managers’ attention on [Logistics Company]s commanding knowledge and expertise, and unique approach to supply chain solutions producing more RFP wins
Industry/Entity Type
Business
Font styles to use
Requirements
Must have
- Slide show, Clearly explain who they are and what they do.
Create an easy to scan design which decreases the reliance on text through featured text, summaries, and smaller “chunked” size bits of information.
Convey [Logistics Company] as high-tech 3PL solutions developer and services
provider with a ‘high-touch’ consultative approach.
Should not have
- No Ads space
No Social media
Not too cluttered. Keep it clean.

```html
<!DOCTYPE html>
<html lang="en">
<head>
<meta charset="utf-8">
<title>Northvale Logistics</title>
<link rel="stylesheet" href="https://fonts.googleapis.com/css2?family=Open+Sans:wght@300;400;600;700&family=Ubuntu:wght@400;500;700&display=swap">
<style>
:root{
  --blue:#1a76b8;
  --blue-deep:#0f5a93;
  --blue-light:#3fb2e6;
  --red:#d3151b;
  --ink:#333;
  --muted:#666;
  --light-bg:#f4f4f4;
  --dark:#2e2e2e;
  --darker:#242424;
  --white:#fff;
}
*{margin:0;padding:0;box-sizing:border-box}
html,body{width:703px;height:1200px;overflow:hidden;background:var(--white)}
body{position:relative;font-family:'Open Sans',Arial,sans-serif;color:var(--ink)}
.abs{position:absolute}

/* header */
.brand{left:64px;top:24px;display:flex;align-items:center;gap:8px}
.brand-dot{width:14px;height:14px;border-radius:50%;background:var(--red)}
.brand-name{font-weight:600;font-size:13px;letter-spacing:3px;color:#222}
.utility-bar{left:370px;top:0;width:268px;height:22px;background:var(--blue-deep);color:var(--white);font-size:8px;display:flex;align-items:center;padding-left:11px;gap:7px;border-bottom:2px solid #0a3f6a;white-space:nowrap}
.utility-bar .phone{margin-left:14px;font-size:10px;display:flex;align-items:center;gap:4px}
.main-nav{top:45px;left:446px;display:flex;gap:21px;font-size:9px;color:var(--blue);white-space:nowrap}

/* hero */
.hero{left:0;top:70px;width:703px;height:316px;overflow:hidden;background:#1f6fae}
.hero-photo{position:absolute;left:0;top:0;width:703px;height:270px;background:radial-gradient(ellipse at 65% 40%,#9fb3c6 0%,#566e86 35%,#2a3a4c 70%,#1c2430 100%)}
.hero-wave{position:absolute;left:0;top:180px}
.hero-title{left:69px;top:74px;color:var(--white)}
.hero-title .lead{font-weight:300;font-size:21px;line-height:26px}
.hero-title .name{font-weight:600;font-size:24px;line-height:30px}
.hero-label{left:65px;top:136px;width:238px;padding:3px 5px;background:rgba(20,25,32,.72);color:var(--white);font-size:8.6px;line-height:11px}
.hero-label b{color:var(--blue-light);font-weight:700;display:block;font-size:9px}
.hero-strap{left:77px;top:273px;width:550px;color:#e8f2fa;font-size:9.6px;line-height:15px}

/* services */
.section-title{font-family:'Ubuntu',sans-serif;font-weight:500;color:var(--blue-deep);font-size:14px}
.services-title{left:65px;top:421px}
.services-rule{left:65px;top:442px;width:573px;height:1px;background:#ddd}
.services-copy{left:67px;top:460px;width:172px;font-size:8px;line-height:11.6px;color:var(--muted)}
.service{width:90px;text-align:center;font-size:9px;color:#555;line-height:12px}
.service .ring{width:68px;height:68px;border-radius:50%;border:1.5px solid var(--blue);margin:0 auto 4px;display:flex;align-items:center;justify-content:center}
.service.active .ring{border-color:var(--red)}
.services-line{left:248px;top:568px}

/* difference row */
.video{left:65px;top:603px;width:161px;height:90px;background:linear-gradient(120deg,#c9d0d4 0%,#707a80 45%,#2f4a3a 100%)}
.video .play{position:absolute;left:66px;top:33px;width:30px;height:22px;border-radius:3px;background:rgba(30,30,30,.8)}
.difference{left:233px;top:602px;width:222px}
.difference h2{font-weight:400;font-size:11.6px;color:#222;margin-bottom:6px}
.difference p{font-size:7.8px;line-height:12.3px;color:#444}
.newsletter{left:463px;top:602px;width:175px;height:91px;background:#4a4a4a;color:var(--white);text-align:center;padding-top:14px;box-shadow:0 8px 8px -6px rgba(0,0,0,.35)}
.newsletter .kicker{font-size:7.4px;font-weight:700}
.newsletter .cta{font-size:8.8px;font-weight:600;margin-top:3px}
.newsletter .field{position:absolute;left:17px;top:52px;width:126px;height:24px;background:var(--white);color:#222;font-size:7.5px;text-align:left;padding:7px}
.newsletter .go{position:absolute;left:135px;top:53px;width:22px;height:22px;border-radius:50%;background:var(--blue-light);border:2px solid var(--white);font-size:8px;line-height:18px;color:var(--white)}

/* lower band */
.lower{left:0;top:728px;width:703px;height:231px;background:var(--light-bg);border-top:1px solid #e6e6e6;border-bottom:1px solid #e6e6e6}
.col-title{top:746px;font-size:12.6px;color:#222;font-weight:400}
.news-item{left:64px;width:166px;font-size:6.7px;line-height:11px;color:#888}
.news-item .head{white-space:nowrap}
.news-item a{color:var(--blue-light);text-decoration:none}
.news-item i{color:var(--blue-light)}
.news-item p{margin-top:7px;color:#777}
.news-sep{left:64px;top:846px;width:158px;height:1px;background:#ddd}
.view-all{font-size:8.8px;font-style:italic;color:#222}
.blog-thumb{left:262px;width:60px;height:60px;background:var(--white);border:1px solid #ddd;padding:5px}
.blog-thumb span{display:block;width:100%;height:100%}
.blog-text{left:328px;width:112px;font-size:7.8px;line-height:12.4px;color:#555}
.blog-date{display:flex;align-items:center;gap:5px;margin-top:6px;font-size:5.6px;color:#aaa}
.quote{left:459px;top:778px;width:180px;height:87px;background:var(--white);border:1px solid #ccc;padding:17px 10px 0 15px;font-size:7.4px;line-height:11.8px;color:#666}
.quote .q{position:absolute;font-size:14px;color:#aaa;font-family:Georgia,serif}
.quote-tip{left:472px;top:864px}
.avatar{left:461px;top:874px;width:36px;height:36px;border-radius:50%;background:linear-gradient(#c8a36a,#6d5646)}
.author{left:502px;top:880px;font-size:8.4px;line-height:12px}
.author b{font-weight:400;color:var(--blue-light);display:block}
.arrow-side{top:810px}

/* footer */
.footer{left:0;top:982px;width:703px;height:188px;background:var(--dark)}
.foot-col{top:1000px;color:#bbb;font-size:7.8px;line-height:11.8px}
.foot-col h3{font-weight:400;font-size:9.2px;color:#ddd;display:flex;align-items:center;gap:8px;margin-bottom:12px}
.foot-col h3::after{content:"";width:38px;height:1px;background:#555}
.foot-brand{left:76px;top:1132px;display:flex;align-items:center;gap:8px}
.foot-brand .dot{width:12px;height:12px;border-radius:50%;background:#777}
.foot-brand .nm{font-weight:600;font-size:11px;letter-spacing:3px;color:#8a8a8a}
.footbar{left:0;top:1170px;width:703px;height:30px;background:var(--darker);color:#aaa;font-size:7.8px}
.footbar .links{position:absolute;left:71px;top:10px;display:flex;gap:12px}
.footbar .legal{position:absolute;right:74px;top:10px;display:flex;gap:8px}
</style>
</head>
<body>

<header>
  <div class="abs brand"><span class="brand-dot"></span><span class="brand-name">NORTHVALE LOGISTICS</span></div>
  <div class="abs utility-bar">
    <span>Company</span><span>|</span><span>Careers</span><span>|</span><span>Contact Us</span>
    <span class="phone"><svg width="9" height="10" viewBox="0 0 9 10"><path d="M2 0.5 L3.6 2.6 L2.6 3.6 Q3.4 5.7 5.4 6.8 L6.4 5.8 L8.5 7.4 L7.3 9.2 Q2.6 8.6 0.6 2 Z" fill="#fff"/></svg>021-555-0148-20</span>
  </div>
  <nav class="abs main-nav"><span>SOLUTIONS</span><span>OUR PROCESS</span><span>INDUSTRIES</span></nav>
</header>

<section class="abs hero">
  <div class="hero-photo" role="img" aria-label="Businessman holding a tablet with a glowing world network of message icons"></div>
  <svg class="hero-wave" width="703" height="136" viewBox="0 0 703 136">
    <defs><linearGradient id="wave" x1="0" y1="0" x2="0" y2="1"><stop offset="0" stop-color="#2b86c8"/><stop offset="1" stop-color="#17659f"/></linearGradient></defs>
    <path d="M0 78 Q250 130 703 40 L703 136 L0 136 Z" fill="#5eaee0"/>
    <path d="M0 84 Q250 135 703 46 L703 136 L0 136 Z" fill="url(#wave)"/>
  </svg>
  <div class="abs hero-title"><div class="lead">Welcome To</div><div class="name">Northvale Logistics</div></div>
  <div class="abs hero-label"><b>ABOUT SUPPLY CHAIN TRANSFORMATION</b>Lorem ipsum dolor sit amet consectetur adipiscing elit, sed do eiusmod tempor incidunt manga aliqua..</div>
  <p class="abs hero-strap">Northvale transforms supply chains by managing complexity, providing data-driven insights and implementing foeward-thinking innovation and actionable strategies that change business results..</p>
</section>

<main>
  <h2 class="abs section-title services-title">Our Services</h2>
  <div class="abs services-rule"></div>
  <p class="abs services-copy">Lorem ipsum dolor sit amet, consectetur adipisicing elit, sed do eiusmod tempor incididunt ut labore et dolore magna aliqua. Ut enim ad minim veniam, quis nostrud exercitation ullamco laboris nisi ut aliquip ex ea commodo consequat. Duis aute irure dolor in reprehenderit in voluptate velit esse cillum dolore eu fugiat nulla pariatur. Excepteur sint</p>

  <div class="abs service active" style="left:233px;top:477px">
    <div class="ring"><svg width="28" height="26" viewBox="0 0 28 26"><path d="M2 25 V12 L8 8 V12 L14 8 V12 L20 8 V3 H24 V25 Z" fill="#d3151b"/><rect x="6" y="16" width="3" height="3" fill="#fff"/><rect x="12" y="16" width="3" height="3" fill="#fff"/><rect x="18" y="16" width="3" height="3" fill="#fff"/><circle cx="23" cy="1.5" r="1.5" fill="#d3151b"/></svg></div>Factory Support</div>
  <div class="abs service" style="left:314px;top:462px">
    <div class="ring"><svg width="28" height="26" viewBox="0 0 28 26"><path d="M1 3 H6 L9 16 H23 L26 6 H8" fill="none" stroke="#1a76b8" stroke-width="2.5"/><path d="M8 7 H25 L22.5 15 H10 Z" fill="#1a76b8"/><circle cx="11" cy="21" r="2.5" fill="#1a76b8"/><circle cx="21" cy="21" r="2.5" fill="#1a76b8"/></svg></div>Retail Distributions</div>
  <div class="abs service" style="left:395px;top:452px">
    <div class="ring"><svg width="28" height="28" viewBox="0 0 28 28"><path d="M4 24 L16 12" stroke="#1a76b8" stroke-width="4" stroke-linecap="round"/><circle cx="19" cy="9" r="6" fill="#1a76b8"/><circle cx="21" cy="7" r="2.6" fill="#fff"/><path d="M6 5 L22 23" stroke="#1a76b8" stroke-width="3.5" stroke-linecap="round"/></svg></div>Aftermarket<br>Support</div>
  <div class="abs service" style="left:476px;top:462px">
    <div class="ring"><svg width="32" height="28" viewBox="0 0 32 28"><circle cx="11" cy="16" r="7" fill="none" stroke="#1a76b8" stroke-width="5" stroke-dasharray="3 2.2"/><circle cx="11" cy="16" r="3" fill="#1a76b8"/><circle cx="24" cy="8" r="5" fill="none" stroke="#1a76b8" stroke-width="4" stroke-dasharray="2.4 1.8"/><circle cx="24" cy="21" r="4" fill="none" stroke="#1a76b8" stroke-width="3.5" stroke-dasharray="2 1.6"/></svg></div>Critical Logistics</div>
  <div class="abs service" style="left:557px;top:477px">
    <div class="ring"><svg width="28" height="28" viewBox="0 0 28 28"><path d="M3 8 H10 A3 3 0 1 1 15 8 H20 V14 A3 3 0 1 0 20 19 V25 H3 Z" fill="#1a76b8"/><path d="M17 2 L25 4 L23 11 L18 9 Z" fill="#4a9ad3"/></svg></div>Supply Chain</div>

  <svg class="abs services-line" width="384" height="14" viewBox="0 0 384 14"><path d="M0 6 H184 L190 12 L196 6 H384" fill="none" stroke="#5c9fd6" stroke-width="1"/></svg>

  <div class="abs video" role="img" aria-label="Video still of two engineers working at a server rack"><span class="play"><svg width="30" height="22" viewBox="0 0 30 22"><path d="M12 6 L19 11 L12 16 Z" fill="#fff"/></svg></span></div>
  <div class="abs difference">
    <h2>The Northvale Difference</h2>
    <p>When you need our help, we will be there! No waiting for days for returned emails. No wondering if your request has been received. We make sure you know you're special to us and that your needs are important.</p>
  </div>
  <div class="abs newsletter">
    <div class="kicker">KEEP UP WITH THE LATEST TRENDS</div>
    <div class="cta">Sign up for our newsletter!</div>
    <div class="field">Enter your email address</div>
    <div class="go">Go</div>
  </div>

  <section class="abs lower"></section>
  <svg class="abs arrow-side" style="left:28px" width="14" height="34" viewBox="0 0 14 34"><path d="M12 1 L2 17 L12 33" fill="none" stroke="#ccc" stroke-width="3"/></svg>
  <svg class="abs arrow-side" style="left:661px" width="14" height="34" viewBox="0 0 14 34"><path d="M2 1 L12 17 L2 33" fill="none" stroke="#ccc" stroke-width="3"/></svg>

  <h2 class="abs col-title" style="left:63px">News and Events</h2>
  <div class="abs news-item" style="top:782px"><div class="head">Hollis Crane Marlborough Sauvignon <a>Blanced etc</a></div><i>posted on March 13, 2014 20:15</i><p>Media release; summer has never tasted better than with Hollis Crane's 2014 Sauvignon Blanc</p></div>
  <div class="abs news-sep"></div>
  <div class="abs news-item" style="top:859px"><div class="head">Hollis Crane Marlborough Sauvignon <a>Blanced etc</a></div><i>posted on March 13, 2014 20:15</i><p>Media release; summer has never tasted better than with Hollis Crane's 2012 Sauvignon Blanc</p></div>
  <span class="abs view-all" style="left:66px;top:921px">View All</span>

  <h2 class="abs col-title" style="left:262px">Our Blog</h2>
  <div class="abs blog-thumb" style="top:783px"><span role="img" aria-label="Person writing at a desk" style="background:linear-gradient(135deg,#3a2a22,#a5866e)"></span></div>
  <div class="abs blog-text" style="top:788px">This in one of the important Blog Post of this website.<div class="blog-date"><svg width="8" height="8" viewBox="0 0 8 8"><rect x=".5" y="1.5" width="7" height="6" fill="none" stroke="#aaa"/><path d="M.5 3.5 H7.5" stroke="#aaa"/></svg>25, JAN, 2011</div></div>
  <div class="abs blog-thumb" style="top:854px"><span role="img" aria-label="Group of colleagues around a table" style="background:linear-gradient(135deg,#ddd,#666)"></span></div>
  <div class="abs blog-text" style="top:859px">This in one of the important Blog Post of this website.<div class="blog-date"><svg width="8" height="8" viewBox="0 0 8 8"><rect x=".5" y="1.5" width="7" height="6" fill="none" stroke="#aaa"/><path d="M.5 3.5 H7.5" stroke="#aaa"/></svg>25, JAN, 2011</div></div>
  <span class="abs view-all" style="left:266px;top:921px">View All</span>

  <h2 class="abs col-title" style="left:458px">Testimonials</h2>
  <div class="abs quote"><span class="q" style="left:5px;top:1px">&ldquo;</span>Lorem Ipsum is simply dummy text of the printing and typesetting industry. Lorem Ipsum has been the industry's standard dummy text ever since the 1500s, when<span class="q" style="right:6px;bottom:-6px">&rdquo;</span></div>
  <svg class="abs quote-tip" width="14" height="7" viewBox="0 0 14 7"><path d="M0 0 H14 L7 7 Z" fill="#3fb2e6"/></svg>
  <div class="abs avatar" role="img" aria-label="Portrait of the testimonial author"></div>
  <div class="abs author"><b>Mara Ellison</b>Manager</div>
  <span class="abs view-all" style="left:461px;top:921px">View All</span>
</main>

<footer>
  <div class="abs footer"></div>
  <div class="abs foot-col" style="left:72px"><h3>Our Process</h3>Concept of operations<br>Supplying the infrastructure<br>Analyzing the data<br>Managing Complexity<br>Providing actionable stratgries<br>nvesting in our clients sucess<br>Driving business results</div>
  <div class="abs foot-col" style="left:226px"><h3>Our Solutions</h3>Business Analytics<br>Geigraphical Coverage<br>Project Financing<br>Project Implementation<br>Technology<br>Quality</div>
  <div class="abs foot-col" style="left:380px"><h3>Industries We Serve</h3>Aerospace<br>Defense<br>Industrial<br>Manifacturing<br>Media &amp; Entertainment<br>Medical<br>Retail<br>Telecom &amp; Electronics</div>
  <div class="abs foot-col" style="left:535px"><h3>Company</h3>Culture<br>Community Involvement<br>Major Metro Presence<br>News<br>Carreers<br>Contact</div>
  <div class="abs foot-brand"><span class="dot"></span><span class="nm">NORTHVALE LOGISTICS</span></div>
  <div class="abs footbar">
    <div class="links"><span>Solutions</span><span>|</span><span>Our Process</span><span>|</span><span>Industries</span></div>
    <div class="legal"><span>© NORTHVALE, INC. 2014</span><span>Privacy Policy</span><span>|</span><span>Term of Use</span></div>
  </div>
</footer>

</body>
</html>
```